New Business Card Design Project

Use the flyer uploaded and website www.brightoakbuilders.com for inspiration.
List Our Services on Backside of business cards
Marcus Delling
Harborline Builders Inc.
Licensed General Contractors
858-471-6093

Contact Information for Business Card

Use the flyer uploaded and website www.brightoakbuilders.com for inspiration. List Our Services on Backside of business cards Marcus Delling Harborline Builders Inc. Licensed General Contractors 858-471-6093

```html
<!DOCTYPE html>
<html lang="en">
<head>
<meta charset="utf-8">
<title>Harborline Builders – Business Card</title>
<link href="https://fonts.googleapis.com/css2?family=Roboto:wght@400;500;700;900&display=swap" rel="stylesheet">
<style>
  :root {
    --stage: #2b2b2d;
    --card: #1e1e21;
    --red: #ec1c24;
    --blue: #4f7fd0;
    --white: #ffffff;
    --photo-light: #eef1f3;
    --photo-mid: #c9d3da;
    --photo-sky: #a9c9e4;
  }
  * { margin: 0; padding: 0; box-sizing: border-box; }
  html, body { width: 1200px; height: 780px; overflow: hidden; }
  body {
    background: var(--stage);
    font-family: "Roboto", Arial, sans-serif;
    color: var(--white);
    position: relative;
  }
  .card {
    position: absolute;
    top: 227px;
    width: 570px;
    height: 326px;
    background: var(--card);
    overflow: hidden;
    box-shadow: 0 10px 30px rgba(0,0,0,.45);
  }
  .card--front { left: 20px; }
  .card--back { left: 610px; }

  /* front */
  .photo { position: absolute; inset: 0; width: 570px; height: 326px; }
  .front-info {
    position: absolute;
    right: 0;
    top: 22px;
    width: 300px;
    text-align: right;
  }
  .brand {
    display: flex;
    align-items: center;
    justify-content: center;
    gap: 7px;
    font-weight: 400;
    letter-spacing: 2px;
    color: var(--white);
  }
  .brand__mark { width: 9px; height: 9px; background: var(--white); }
  .front-info .brand { font-size: 15px; margin: 0 30px 28px 0; justify-content: flex-end; }
  .person { display: flex; justify-content: flex-end; align-items: center; gap: 10px; }
  .person__name { font-size: 31px; font-weight: 900; color: var(--red); line-height: 1; }
  .person__bar { width: 28px; height: 26px; background: var(--red); }
  .person__title { font-size: 13.5px; font-weight: 500; margin: 4px 38px 14px 0; }
  .company { font-size: 13px; font-weight: 500; margin: 0 38px 14px 0; }
  .contact { list-style: none; margin-right: 16px; }
  .contact li {
    display: flex; justify-content: flex-end; align-items: center; gap: 8px;
    font-size: 12.5px; font-weight: 500; line-height: 20px;
  }
  .contact svg { width: 13px; height: 13px; fill: var(--red); }

  /* back */
  .card--back .brand { font-size: 26px; margin-top: 78px; letter-spacing: 3px; }
  .card--back .brand__mark { width: 14px; height: 14px; }
  .guarantee {
    margin-top: 38px;
    text-align: center;
    font-size: 15px;
    font-weight: 900;
    color: var(--red);
    letter-spacing: .3px;
  }
  .specialty {
    display: flex; align-items: center; gap: 10px;
    margin: 2px 0 10px;
    font-size: 14px; font-weight: 900; color: var(--blue);
  }
  .specialty::before, .specialty::after {
    content: ""; flex: 1; height: 2px; background: var(--blue);
  }
  .services { list-style: none; text-align: center; padding: 0 12px; }
  .services li { font-size: 11.8px; font-weight: 500; line-height: 19px; }
  .services span { white-space: nowrap; margin: 0 3px; }
  .tick { width: 10px; height: 10px; vertical-align: -1px; margin-right: 3px; }
</style>
</head>
<body>
<svg width="0" height="0" style="position:absolute">
  <symbol id="tick" viewBox="0 0 12 12">
    <circle cx="6" cy="6" r="5" fill="none" stroke="#ec1c24" stroke-width="1.3"/>
    <path d="M3.3 6.2l2 2 4.4-5" fill="none" stroke="#ec1c24" stroke-width="1.6" stroke-linecap="round"/>
  </symbol>
</svg>

<section class="card card--front">
  <svg class="photo" viewBox="0 0 570 326">
    <defs>
      <linearGradient id="interior" x1="0" y1="0" x2="1" y2="1">
        <stop offset="0" stop-color="var(--photo-sky)"/>
        <stop offset=".45" stop-color="var(--photo-light)"/>
        <stop offset="1" stop-color="var(--photo-mid)"/>
      </linearGradient>
    </defs>
    <path role="img" aria-label="Photo of a bright modern living room with tall windows and white sofas"
          d="M0 0 C140 20 270 120 300 326 L0 326 Z" fill="url(#interior)"/>
    <path d="M0 -4 C140 16 274 118 306 326" fill="none" stroke="var(--red)" stroke-width="9"/>
  </svg>

  <div class="front-info">
    <div class="brand"><span class="brand__mark"></span>HARBORLINE BUILDERS</div>
    <div class="person">
      <h1 class="person__name">Marcus Delling</h1>
      <span class="person__bar"></span>
    </div>
    <p class="person__title">Licensed General Contractors</p>
    <p class="company">Harborline Builders Inc.</p>
    <ul class="contact">
      <li>858-471-6093
        <svg viewBox="0 0 24 24"><path d="M6.6 10.8a15.2 15.2 0 0 0 6.6 6.6l2.2-2.2a1 1 0 0 1 1-.25 11.4 11.4 0 0 0 3.6.57 1 1 0 0 1 1 1V20a1 1 0 0 1-1 1A17 17 0 0 1 3 4a1 1 0 0 1 1-1h3.5a1 1 0 0 1 1 1c0 1.25.2 2.45.57 3.57a1 1 0 0 1-.25 1z"/></svg>
      </li>
      <li>info@brightoakbuilders.com
        <svg viewBox="0 0 24 24"><path d="M3 5h18v14H3z M3 5l9 7 9-7" fill="none" stroke="#ec1c24" stroke-width="2.4"/></svg>
      </li>
      <li>www.brightoakbuilders.com
        <svg viewBox="0 0 24 24"><circle cx="12" cy="12" r="9" fill="none" stroke="#ec1c24" stroke-width="2.2"/><path d="M3 12h18M12 3c3 3 3 15 0 18M12 3c-3 3-3 15 0 18" fill="none" stroke="#ec1c24" stroke-width="1.8"/></svg>
      </li>
    </ul>
  </div>
</section>

<section class="card card--back">
  <div class="brand"><span class="brand__mark"></span>HARBORLINE BUILDERS</div>
  <p class="guarantee">OUR SERVICES ARE 100% GUARANTEED</p>
  <p class="specialty">SPECIALIZING IN:</p>
  <ul class="services">
    <li>
      <span><svg class="tick"><use href="#tick"/></svg>Remodel: Kitchen &amp; Bath</span>
      <span><svg class="tick"><use href="#tick"/></svg>Painting: Interior &amp; Exterior</span>
      <span><svg class="tick"><use href="#tick"/></svg>Flooring: Carpet, Vinyl, Wood</span>
    </li>
    <li>
      <span><svg class="tick"><use href="#tick"/></svg>Window &amp; Door Replacement</span>
      <span><svg class="tick"><use href="#tick"/></svg>Plumbing: Repairs &amp; Upgrades</span>
      <span><svg class="tick"><use href="#tick"/></svg>Energy-Efficient Upgrades</span>
    </li>
    <li>
      <span><svg class="tick"><use href="#tick"/></svg>Deck &amp; Patio Construction</span>
      <span><svg class="tick"><use href="#tick"/></svg>Water &amp; Mold Damage</span>
      <span><svg class="tick"><use href="#tick"/></svg>Garage Renovation</span>
    </li>
  </ul>
</section>
</body>
</html>
```